Alaska Law Firm Needs a Sticker Design

We need a design for stickers to put on already-printed brochures. We mail the brochures to potential clients so they can learn more about accident-induced injuries, insurance claims, legal representation, and our own law firm.

One of our lawyers wrote a book that provides a helpful overview of personal injury claims. We are offering this book for free to anyone who calls and requests it. Therefore, the sticker design should include one of the following phrases, or something very similar:
a) "Still have questions? Call and request our book-- for free!"
b) "Still have questions about auto accident claims? Call and request our book today."
c) "Still have questions about filing a claim? Call and request a free copy of our book."
d) "Still have questions? Call us today to request a free copy of our book, Clear Lanes Ahead."
e) "To learn more about automobile accidents and insurance, call today and request a free copy of our book."

The sticker should be approximately 3"x3" and may be a circle, square, rectangle, or ellipsis. The sticker will be placed on the back of the folder, which is light blue. We would like the sticker to match the color scheme of our website and the folder.

I will upload an image of the book cover as soon as I obtain it.

Law Firm

Font styles to use
Serif
Sans Serif

Requirements
Should not have
• Bright colors that aren't already used in the folder design. e.g. no bright orange, pink, chartreuse, turquoise, yellow, red.

```html
<!DOCTYPE html>
<html lang="en">
<head>
<meta charset="utf-8">
<title>Still Have Questions Sticker</title>
<link rel="stylesheet" href="https://fonts.googleapis.com/css2?family=Rye&family=Kurale&family=Overlock:wght@900&display=swap">
<style>
  :root {
    --page: #ececec;
    --navy: #1b2672;
    --band: #1e2b80;
    --royal: #22339a;
    --ink: #262626;
    --paper: #ffffff;
  }
  html, body {
    margin: 0;
    padding: 0;
    width: 1200px;
    height: 1200px;
    overflow: hidden;
    background: var(--page);
  }
  .sticker {
    display: block;
    width: 1200px;
    height: 1200px;
  }
  .sticker__body { fill: var(--paper); }
  .sticker__rim { fill: none; stroke: var(--navy); stroke-width: 14; }
  .sticker__band { fill: var(--band); }
  .headline {
    font-family: "Rye", serif;
    text-anchor: middle;
  }
  .headline--still { fill: var(--ink); font-size: 150px; }
  .headline--have { fill: var(--royal); font-size: 150px; }
  .headline--questions { fill: var(--paper); font-size: 118px; }
  .offer {
    font-family: "Kurale", serif;
    font-size: 46px;
    fill: var(--ink);
    text-anchor: middle;
  }
  .price {
    font-family: "Overlock", sans-serif;
    font-weight: 900;
    fill: var(--royal);
    text-anchor: middle;
  }
  .price--for { font-size: 160px; }
  .price--free { font-size: 118px; }
  .spark { stroke: var(--royal); stroke-width: 6; stroke-linecap: round; }
</style>
</head>
<body>
<svg class="sticker" viewBox="0 0 1200 1200" xmlns="http://www.w3.org/2000/svg" role="img" aria-label="Still have questions? Call and request our book for free!">
  <defs>
    <clipPath id="badge-shape">
      <path d="M600 1135 C430 1030 230 860 170 700 A452 452 0 1 1 1030 700 C970 860 770 1030 600 1135 Z"/>
    </clipPath>
    <filter id="lift" x="-10%" y="-30%" width="120%" height="160%">
      <feDropShadow dx="3" dy="4" stdDeviation="3" flood-color="#000" flood-opacity="0.45"/>
    </filter>
  </defs>

  <path class="sticker__body" d="M600 1135 C430 1030 230 860 170 700 A452 452 0 1 1 1030 700 C970 860 770 1030 600 1135 Z"/>
  <rect class="sticker__band" x="100" y="519" width="1000" height="152" clip-path="url(#badge-shape)"/>
  <path class="sticker__rim" d="M600 1135 C430 1030 230 860 170 700 A452 452 0 1 1 1030 700 C970 860 770 1030 600 1135 Z"/>

  <text class="headline headline--still" x="600" y="309" textLength="395" lengthAdjust="spacingAndGlyphs">STILL</text>
  <text class="headline headline--have" x="598" y="478" textLength="424" lengthAdjust="spacingAndGlyphs">HAVE</text>
  <text class="headline headline--questions" x="616" y="637" textLength="724" lengthAdjust="spacingAndGlyphs" filter="url(#lift)">QUESTIONS?</text>

  <text class="offer" x="614" y="734" textLength="498" lengthAdjust="spacingAndGlyphs">Call and request our book</text>

  <g class="spark" transform="translate(399 824)">
    <line x1="-22" y1="0" x2="22" y2="0"/>
    <line x1="0" y1="-22" x2="0" y2="22"/>
    <line x1="-16" y1="-16" x2="16" y2="16"/>
    <line x1="-16" y1="16" x2="16" y2="-16"/>
  </g>
  <g class="spark" transform="translate(789 824)">
    <line x1="-22" y1="0" x2="22" y2="0"/>
    <line x1="0" y1="-22" x2="0" y2="22"/>
    <line x1="-16" y1="-16" x2="16" y2="16"/>
    <line x1="-16" y1="16" x2="16" y2="-16"/>
  </g>

  <text class="price price--for" x="598" y="891" textLength="268" lengthAdjust="spacingAndGlyphs">FOR</text>
  <text class="price price--free" x="598" y="988" textLength="252" lengthAdjust="spacingAndGlyphs">FREE!</text>
</svg>
</body>
</html>
```